Halverstone Minerals Web Design

Require a Web page design for an international mining and private investment company currently based in Dubai, UAE. I would like to view designs that incorporate our current corporate logo design aimed at communicating global business development/expansion across a diversity of commodities within the mining and investment sectors.

We are a global organisation with global experience and strategy with specific business development focus in Africa, Central and South America.

Target Market(s)

Mining industry, finance, fund raising, brokering, private equity and public stock exchanges.

Industry/Entity Type

Mining

Number of Pages Required

5+ page

Font styles to use
Sans Serif

Colors

Designer to choose colors to be used in the design.

Requirements
Must have
• Corporate logo, description of who we are, what we do, corporate mission, vision & strategy.
Nice to have
• Inclusion of images, photos, interactive maps/graphics and video.

```html
<!DOCTYPE html>
<html lang="en">
<head>
<meta charset="utf-8">
<title>Halverstone Minerals</title>
<link href="https://fonts.googleapis.com/css2?family=Open+Sans:ital,wght@0,400;0,600;0,700;1,400&family=Oswald:wght@600&display=swap" rel="stylesheet">
<style>
:root{
  --gold:#c9a448;
  --gold-dark:#a8852e;
  --ink:#222;
  --text:#555;
  --white:#fff;
  --grey-band:#e6e6e6;
  --dark:#1c1c1c;
  --blue:#3a78c2;
}
*{box-sizing:border-box;margin:0;padding:0}
html,body{width:1200px;height:4255px;overflow:hidden}
body{font-family:"Open Sans",Arial,sans-serif;color:var(--ink);background:var(--white);position:relative}
section,header,footer{position:absolute;left:0;width:1200px}

/* header */
.site-header{top:0;height:108px;background:var(--white)}
.brand{position:absolute;display:flex;align-items:center;gap:10px;color:var(--gold);font-weight:700;font-size:20px;letter-spacing:.5px}
.brand-mark{width:22px;height:22px;background:var(--gold)}
.site-header .brand{left:85px;top:38px}
.main-nav{position:absolute;right:92px;top:42px;display:flex;gap:28px;font-size:15px}
.main-nav a{color:var(--ink);text-decoration:none}
.main-nav a.active{color:var(--gold)}

/* hero */
.hero{top:108px;height:590px;overflow:hidden}
.hero-photo{position:absolute;inset:0;background:linear-gradient(180deg,#55585c 0%,#3d4145 45%,#2a2d30 100%)}
.hero-title{position:absolute;top:160px;width:100%;text-align:center;font-family:"Oswald",Arial,sans-serif;font-weight:600;font-size:58px;color:var(--white);letter-spacing:1px}
.hero-sub{position:absolute;top:242px;width:100%;text-align:center;font-size:33px;color:var(--white)}
.hero-btn{position:absolute;top:315px;left:513px;width:172px;height:44px;border:2px solid var(--white);color:var(--white);font-size:15px;font-weight:600;display:flex;align-items:center;justify-content:center;letter-spacing:.5px}
.hero-arrow{position:absolute;top:268px;width:26px;height:26px;border-radius:50%;background:rgba(0,0,0,.45)}
.hero-arrow.prev{left:68px}.hero-arrow.next{right:68px}
.hero-edge{position:absolute;bottom:0;left:0}

/* about */
.about{top:894px;height:340px}
.about-box{position:absolute;left:85px;top:0;width:555px;height:340px;border:2px solid var(--gold);padding:40px 30px 0 40px}
.about-box h2{font-weight:400;font-size:36px;margin-bottom:18px}
.about-box p{font-size:14.5px;line-height:25px;color:var(--text);margin-bottom:12px}
.about-media{position:absolute;left:600px;top:6px;width:515px;height:330px;background:radial-gradient(circle at 55% 55%,#c79b3b 0%,#5a4424 25%,#2b231a 60%,#1a1612 100%)}

/* services */
.services{top:1348px;height:604px;background:var(--grey-band)}
.notch{position:absolute;left:585px;top:0}
.section-title{position:absolute;width:100%;text-align:center;font-weight:400;font-size:32px}
.services .section-title{top:80px}
.service-card{position:absolute;top:224px;width:222px;height:258px;background:var(--white);box-shadow:0 2px 8px rgba(0,0,0,.15);text-align:center;padding:62px 18px 0}
.service-icon{position:absolute;top:-38px;left:71px;width:80px;height:80px;border-radius:50%;background:var(--gold);display:flex;align-items:center;justify-content:center}
.service-card h3{font-weight:600;font-size:17px;margin-bottom:14px}
.service-card p{font-size:12px;line-height:18px;color:var(--text)}
.read-more{display:inline-block;margin-top:22px;font-size:13px;font-weight:600;color:var(--ink);padding-bottom:5px;border-bottom:2px solid var(--gold);letter-spacing:.3px}

/* about us */
.who{top:1952px;height:545px;overflow:hidden}
.who-photo{position:absolute;inset:0;background:linear-gradient(180deg,#3a3324 0%,#4a3f28 50%,#2e281e 100%)}
.who .section-title{top:78px;color:var(--white)}
.who-card{position:absolute;top:176px;width:494px;height:230px;display:flex}
.who-media{width:230px;height:230px}
.who-body{flex:1;background:#141414;padding:26px 20px 0;color:var(--white)}
.who-body h3{font-size:17px;font-weight:600;margin-bottom:14px}
.who-body p{font-size:13px;line-height:21px}
.who-body .more{margin-top:10px;font-size:13px;font-weight:600}
.who-edge{position:absolute;bottom:0;left:0}

/* news */
.news{top:2567px;height:600px}
.news .section-title{top:58px}
.news-card{position:absolute;top:148px;width:502px;height:445px;border:1px solid #ddd}
.news-media{height:235px}
.news-body{padding:20px 38px}
.news-date{font-size:13px;color:var(--gold);margin-bottom:12px}
.news-body h3{font-weight:400;font-size:20px;margin-bottom:12px}
.news-body p{font-size:13px;line-height:21px;color:var(--text)}
.news-body .read-more{border-color:var(--blue);margin-top:14px}

/* testimonial */
.testimonial{top:3263px;height:560px;overflow:hidden}
.testimonial-photo{position:absolute;inset:0;background:linear-gradient(180deg,#2b2b2b 0%,#383838 60%,#2a2a2a 100%)}
.testimonial .section-title{top:88px;color:var(--white)}
.quote{position:absolute;top:196px;left:120px;width:960px;text-align:center;color:var(--white);font-size:15px;line-height:29px}
.quote-mark{position:absolute;font-family:Georgia,serif;font-size:44px;color:var(--white);font-weight:700;line-height:1}
.testimonial-nav{position:absolute;top:318px;left:0;width:100%;display:flex;justify-content:center;align-items:center;gap:40px}
.avatar{width:110px;height:110px;border-radius:50%;border:4px solid var(--white);background:linear-gradient(135deg,#b88a62,#6e5240)}
.author{position:absolute;top:442px;width:100%;text-align:center;color:var(--white);font-style:italic;font-size:15px}

/* footer */
.site-footer{top:3816px;height:439px;background:linear-gradient(180deg,#fff 0%,#f3f3f3 70%,#e4e4e4 100%)}
.site-footer .brand{left:455px;top:90px;font-size:26px}
.footer-nav{position:absolute;top:168px;width:100%;display:flex;justify-content:center;font-size:14px}
.footer-nav a{color:var(--ink);text-decoration:none;padding:0 10px;border-left:1px solid #999}
.footer-nav a:first-child{border-left:0}
.social{position:absolute;top:228px;width:100%;display:flex;justify-content:center;gap:12px}
.social span{width:40px;height:40px;border-radius:50%;border:2px solid var(--ink)}
.copyright{position:absolute;top:298px;width:100%;text-align:center;font-size:12px;color:var(--text)}
.footer-scene{position:absolute;bottom:0;left:0;width:1200px;height:80px;background:linear-gradient(180deg,rgba(40,40,40,0) 0%,#3a3a3a 70%,#222 100%)}
</style>
</head>
<body>

<header class="site-header">
  <div class="brand"><span class="brand-mark"></span>Halverstone Minerals</div>
  <nav class="main-nav">
    <a class="active" href="#">Home</a><a href="#">Who we are</a><a href="#">What we do</a><a href="#">Corporate mission</a><a href="#">Vision &amp; strategy</a><a href="#">Contact us</a>
  </nav>
</header>

<section class="hero">
  <div class="hero-photo" role="img" aria-label="Open-pit mine with yellow haul trucks"></div>
  <h1 class="hero-title">HALVERSTONE MINERALS</h1>
  <p class="hero-sub">International mining and private investment</p>
  <div class="hero-btn">LEARN MORE</div>
  <span class="hero-arrow prev"></span><span class="hero-arrow next"></span>
  <svg class="hero-edge" width="1200" height="110" viewBox="0 0 1200 110">
    <polygon fill="#fff" points="0,85 90,80 130,100 200,95 260,110 330,96 400,105 520,88 600,100 680,84 730,96 820,100 870,88 960,92 1040,82 1100,96 1160,84 1200,78 1200,110 0,110"/>
    <g fill="#5b8fd0"><circle cx="75" cy="84" r="3"/><circle cx="205" cy="96" r="3"/><circle cx="400" cy="105" r="3"/><circle cx="520" cy="88" r="3"/><circle cx="730" cy="96" r="3"/><circle cx="850" cy="94" r="3"/><circle cx="1040" cy="82" r="3"/><circle cx="1180" cy="81" r="3"/></g>
  </svg>
</section>

<section class="about">
  <div class="about-box">
    <h2>About</h2>
    <p>It is a long established fact that a reader will be distracted by the readable content of a page when looking at its layout. The point of using Lorem Ipsum is that it has a more-or-less here, content here',</p>
    <p>Many desktop publishing packages and web page editors now use Lorem Ipsum as their default model text, and a search for 'lorem ipsum' will uncover many web sites</p>
  </div>
  <div class="about-media" role="img" aria-label="Video still of a shovel and glowing gold coins on soil"></div>
</section>

<section class="services">
  <svg class="notch" width="30" height="16" viewBox="0 0 30 16"><polygon fill="#fff" points="0,0 30,0 15,14"/></svg>
  <h2 class="section-title">What we do</h2>
  <div class="service-card" style="left:88px">
    <div class="service-icon"><svg width="34" height="34" viewBox="0 0 34 34" fill="none" stroke="#fff" stroke-width="3"><circle cx="19" cy="6" r="3" fill="#fff"/><path d="M18 11 14 21l6 4v7M14 21l-5 10M16 14l8 4M6 10l8 4"/></svg></div>
    <h3>Mining</h3>
    <p>It is a long established fact that a reader will be tracted by the readable content of a page when looking</p>
    <span class="read-more">READ MORE</span>
  </div>
  <div class="service-card" style="left:348px">
    <div class="service-icon"><svg width="34" height="34" viewBox="0 0 34 34" fill="none" stroke="#fff" stroke-width="3"><circle cx="20" cy="11" r="8"/><path d="M3 24h8l6 3h9l5-4M3 31h22"/></svg></div>
    <h3>Investment</h3>
    <p>It is a long established fact that a reader will be is tracted by the readable content of a page when looking</p>
    <span class="read-more">READ MORE</span>
  </div>
  <div class="service-card" style="left:610px">
    <div class="service-icon"><svg width="30" height="30" viewBox="0 0 30 30"><circle cx="15" cy="15" r="10" fill="none" stroke="#fff" stroke-width="6" stroke-dasharray="4 3"/><circle cx="15" cy="15" r="4" fill="#fff"/></svg></div>
    <h3>Vision &amp; strategy</h3>
    <p>It is a long established fact that a reader will be is tracted by the readable content of a page when looking</p>
    <span class="read-more">READ MORE</span>
  </div>
  <div class="service-card" style="left:868px">
    <div class="service-icon"><svg width="26" height="30" viewBox="0 0 26 30"><path d="M2 2h15l7 7v19H2z" fill="#fff"/><path d="M7 14h12M7 19h12M7 24h8" stroke="#c9a448" stroke-width="2"/></svg></div>
    <h3>Corporate mission</h3>
    <p>It is a long established fact that a reader will be is tracted by the readable content of a page when looking</p>
    <span class="read-more">READ MORE</span>
  </div>
</section>

<section class="who">
  <div class="who-photo" role="img" aria-label="Mining excavators at a dusky quarry"></div>
  <h2 class="section-title">Who we are</h2>
  <div class="who-card" style="left:92px">
    <div class="who-media" role="img" aria-label="Business team reviewing charts" style="background:linear-gradient(135deg,#d8dde3,#8a96a6)"></div>
    <div class="who-body"><h3>Porro quisquam</h3><p>It is a long established fact that a reader will be distracted by the readable content of a page when looking at its layout. The point of using Lorem</p><p class="more">READ MORE</p></div>
  </div>
  <div class="who-card" style="left:618px">
    <div class="who-media" role="img" aria-label="Stacks of coins" style="background:linear-gradient(135deg,#4f6a84,#a9b3bc)"></div>
    <div class="who-body"><h3>Porro quisquam</h3><p>It is a long established fact that a reader will be distracted by the readable content of a page when looking at its layout. The point of using Lorem</p><p class="more">READ MORE</p></div>
  </div>
  <svg class="who-edge" width="1200" height="70" viewBox="0 0 1200 70"><polygon fill="#fff" points="0,40 70,30 130,52 220,40 300,62 380,45 470,58 560,42 640,55 720,38 800,50 900,44 980,58 1060,36 1140,48 1200,30 1200,70 0,70"/></svg>
</section>

<section class="news">
  <h2 class="section-title">Latest News</h2>
  <article class="news-card" style="left:88px">
    <div class="news-media" role="img" aria-label="Glass jar of coins with a sprouting plant" style="background:linear-gradient(180deg,#b8d68a,#6c8f3a 60%,#4a3a26)"></div>
    <div class="news-body"><p class="news-date">MARCH 20, 2018</p><h3>Neque porro quisquam est qui</h3><p>Praesent elementum elit at tellus nec ultricies sit amet porttitor mattis enim In massa libero interdum nec interdum vel blandi</p><span class="read-more">READ MORE</span></div>
  </article>
  <article class="news-card" style="left:608px">
    <div class="news-media" role="img" aria-label="Yellow dump trucks on a coal mine" style="background:linear-gradient(180deg,#6f7378,#3b3d40 60%,#1f2022)"></div>
    <div class="news-body"><p class="news-date">MARCH 20, 2018</p><h3>Dolorem ipsum quia dolor sit amet</h3><p>Praesent elementum elit at tellus nec ultricies sit amet porttitor mattis enim In massa libero interdum nec interdum</p><span class="read-more">READ MORE</span></div>
  </article>
</section>

<section class="testimonial">
  <div class="testimonial-photo" role="img" aria-label="Dark coal mine landscape with haul trucks"></div>
  <svg class="notch" width="30" height="16" viewBox="0 0 30 16"><polygon fill="#fff" points="0,0 30,0 15,14"/></svg>
  <h2 class="section-title">Testimonial</h2>
  <span class="quote-mark" style="left:108px;top:205px">&ldquo;</span>
  <p class="quote">It has survived not only five centuries, but also the leap into electronic typesetting, remaining essentially unchanged. It was popularised in the 1960s with the release of Linotrace sheets containing Lorem Ipsum passages, and more recently with desktop publishing software like Ardell PageSetter including versions of Lorem Ipsum</p>
  <span class="quote-mark" style="left:958px;top:262px">&rdquo;</span>
  <div class="testimonial-nav">
    <svg width="16" height="26" viewBox="0 0 16 26"><path d="M14 2 3 13l11 11" fill="none" stroke="#fff" stroke-width="3"/></svg>
    <div class="avatar" role="img" aria-label="Portrait of the client"></div>
    <svg width="16" height="26" viewBox="0 0 16 26"><path d="M2 2l11 11L2 24" fill="none" stroke="#fff" stroke-width="3"/></svg>
  </div>
  <p class="author">Neque porro quisquam</p>
  <svg class="who-edge" width="1200" height="70" viewBox="0 0 1200 70"><polygon fill="#fff" points="0,38 90,52 160,34 250,48 330,30 420,55 500,40 600,58 690,36 770,50 860,32 950,54 1030,40 1110,56 1200,36 1200,70 0,70"/></svg>
</section>

<footer class="site-footer">
  <div class="brand"><span class="brand-mark"></span>Halverstone Minerals</div>
  <nav class="footer-nav"><a href="#">Home</a><a href="#">Who we are</a><a href="#">What we do</a><a href="#">Corporate mission</a><a href="#">Vision &amp; strategy</a><a href="#">Contact us</a></nav>
  <div class="social"><span></span><span></span><span></span><span></span><span></span></div>
  <p class="copyright">Copyright © 2018 All Rights Reserved</p>
  <div class="footer-scene" role="img" aria-label="Silhouette of mining machinery along the ground"></div>
</footer>

</body>
</html>
```